Website Design for a holiday home letting busines

We require a redesign of our present website www.pinebrookstays.com. We want the website to stand out and look professional and clean to make holiday hunters want to book a caravan or lodge holiday with us. Our logo is red however we DO NOT want the website to be red. We want a natural colour scheme.

The final design should communicate that we are a professional company to book with.

On the home page we require;
Overview of company
Photo
Search box for holiday (check in)
Late Deals
Reviews
News

We would like the following pages designed; home page, available dates page, caravans page, content page.

The website should be responsive for smart phones. One website I do like is http://www.verdoliso.be/nl/

Target Market(s)

Families

Industry/Entity Type

Travel

Number of Pages Required

5+ page

Font styles to use
Serif

Requirements
Must have
• The project must be responsive for mobile phones and tablets.
• Ability to search for holiday home holidays
• We want a natural colour scheme.
Nice to have
• A style we like is http://www.verdoliso.be/nl/
Should not have
• Do not use red as a colour for the website. Our logo is red so this is the only time we want this used.

```html
<!DOCTYPE html>
<html lang="en">
<head>
<meta charset="utf-8">
<title>Pinebrook Stays – Holiday Lodges &amp; Caravans</title>
<link href="https://fonts.googleapis.com/css2?family=Open+Sans:wght@400;600;700&family=Merriweather:wght@400;700&display=swap" rel="stylesheet">
<style>
:root{
  --blue:#1f8fcb;
  --blue-dark:#16709f;
  --ink:#333a40;
  --muted:#7a8288;
  --line:#e3e6e8;
  --paper:#ffffff;
  --soft:#f4f6f7;
  --footer:#2a2f33;
  --footer-deep:#1f2326;
  --charcoal:#2c2f31;
  --accent:#b8262c;
  --veil:rgba(8,12,16,.72);
  --photo-light:#a9bccb;
  --photo-deep:#4f7f95;
}
*{box-sizing:border-box;margin:0;padding:0}
html,body{width:1200px;height:2540px;overflow:hidden}
body{position:relative;background:var(--paper);font-family:"Open Sans",Arial,sans-serif;color:var(--ink);font-size:14px;line-height:1.5}
.section{position:absolute;left:0;width:1200px}
h2,h3,h4{font-family:"Merriweather",Georgia,serif;font-weight:700}

/* header */
.site-header{top:0;height:140px;background:var(--paper)}
.brand{position:absolute;left:92px;top:42px;display:flex;align-items:center;gap:12px}
.brand-dot{width:38px;height:38px;border-radius:50%;background:var(--accent)}
.brand-name{font-family:"Merriweather",Georgia,serif;font-size:20px;color:var(--ink);font-weight:700}
.header-contact{position:absolute;left:580px;top:54px;display:flex;gap:36px;color:var(--muted);font-size:13px}
.header-contact span{display:flex;align-items:center;gap:6px}
.header-cta{position:absolute;left:1008px;top:50px;width:90px;height:28px;background:var(--blue);color:#fff;font-size:12px;font-weight:600;text-align:center;line-height:28px}

/* hero */
.hero{top:140px;height:500px;background:linear-gradient(180deg,#8c7a62 0%,#6a5a48 45%,#a89478 100%)}
.main-nav{position:absolute;left:100px;top:28px;width:1000px;height:42px;background:rgba(255,255,255,.92);display:flex}
.main-nav a{display:block;padding:0 26px;line-height:42px;font-size:13px;color:var(--ink);text-decoration:none;font-weight:600}
.main-nav a.active{background:var(--blue);color:#fff}

/* intro */
.intro{top:750px;text-align:center;color:var(--muted);font-size:14px}
.intro p{width:840px;margin:0 auto}

/* deal cards */
.section-title{font-size:20px;color:var(--blue);text-align:center}
.deals{top:862px}
.reviews-strip{top:1452px}
.card-row{position:absolute;left:120px;top:110px;width:960px;display:grid;grid-template-columns:repeat(5,1fr);gap:48px}
.reviews-strip .card-row{top:108px}
.card-photo{height:156px;background:linear-gradient(160deg,#c9b79a,#8a735a)}
.card-row .card:nth-child(2n) .card-photo{background:linear-gradient(160deg,#b9a68c,#6e5a46)}
.card-title{margin-top:10px;font-size:13px;font-weight:700;color:var(--blue)}
.card-meta{font-size:12px;color:var(--muted)}
.card-meta b{color:var(--ink)}

/* search band */
.search-band{top:1292px;height:140px;background:var(--blue)}
.search-band h3{text-align:center;color:#fff;font-size:17px;padding-top:22px}
.search-form{position:absolute;left:100px;top:72px;width:1000px;display:flex;align-items:center;gap:24px;color:#eaf5fb;font-size:13px}
.search-field{height:26px;border-bottom:1px solid rgba(255,255,255,.5);padding:0 4px;line-height:26px}
.search-field.wide{width:230px}
.search-field.mid{width:150px}
.search-btn{margin-left:auto;width:160px;height:30px;background:var(--charcoal);color:#fff;text-align:center;line-height:30px;font-weight:600}

/* lower columns */
.lower{top:1920px;height:300px}
.col{position:absolute;top:0}
.col h4{font-size:14px;color:var(--ink);margin-bottom:14px}
.col-reviews{left:100px;width:320px}
.col-news{left:460px;width:300px}
.col-side{left:812px;width:260px}
.review{display:flex;gap:10px;margin-bottom:18px;font-size:12px;color:var(--muted)}
.review .stamp{flex:0 0 18px;height:18px;border-radius:50%;background:var(--blue)}
.news-item{font-size:12px;color:var(--muted);margin-bottom:14px}
.news-item .date{color:var(--blue);font-weight:600}
.side-head{background:var(--blue);color:#fff;font-size:13px;font-weight:700;padding:10px 12px}
.side-item{display:flex;gap:10px;align-items:center;padding:8px 0;border-bottom:1px solid var(--line);font-size:12px;color:var(--muted)}
.side-thumb{width:26px;height:26px;background:linear-gradient(160deg,#b9a68c,#6e5a46)}

/* footer */
.site-footer{top:2248px;height:292px;background:var(--footer);color:#aab1b6;font-size:12px}
.fcol{position:absolute;top:34px}
.fcol h5{color:#fff;font-size:13px;margin-bottom:12px}
.fcol p{margin-bottom:6px}
.f-news{left:100px;width:240px}
.f-input{width:240px;height:26px;background:#fff;margin-top:14px}
.f-btn{width:140px;height:26px;background:var(--blue);color:#fff;text-align:center;line-height:26px;margin-top:12px;font-weight:600}
.f-links{left:400px}
.f-more{left:680px}
.f-info{left:840px}
.f-social{left:1020px}
.social-dot{width:18px;height:18px;border-radius:50%;background:#6b7379;margin-bottom:12px}
.copyright{position:absolute;left:0;bottom:0;width:1200px;height:40px;background:var(--footer-deep);text-align:center;line-height:40px;font-size:11px}

/* newsletter modal */
.veil{position:absolute;inset:0;background:var(--veil)}
.modal{position:absolute;left:232px;top:388px;width:748px;height:340px;border:6px solid #fff;background:#fff}
.modal-photo{position:absolute;inset:0;background:linear-gradient(135deg,var(--photo-light) 0%,var(--photo-deep) 100%)}
.modal-form{position:absolute;left:90px;top:142px;display:flex}
.modal-input{width:432px;height:48px;background:var(--blue);color:#e8f4fb;font-size:13px;line-height:48px;padding-left:18px}
.modal-submit{width:100px;height:48px;background:var(--charcoal);color:#fff;font-weight:700;font-size:13px;text-align:center;line-height:48px}
.modal-close{position:absolute;right:-22px;top:-22px;width:30px;height:30px}
</style>
</head>
<body>

<header class="section site-header">
  <div class="brand"><span class="brand-dot"></span><span class="brand-name">Pinebrook Stays</span></div>
  <div class="header-contact">
    <span><svg width="12" height="12" viewBox="0 0 12 12"><path d="M2 1h3l1 3-2 1a7 7 0 0 0 3 3l1-2 3 1v3c-6 1-10-3-9-9z" fill="#7a8288"/></svg>+44 1632 960418</span>
    <span><svg width="12" height="12" viewBox="0 0 12 12"><rect x="1" y="2.5" width="10" height="7" fill="none" stroke="#7a8288"/><path d="M1 3l5 4 5-4" fill="none" stroke="#7a8288"/></svg>hello@pinebrookstays.com</span>
  </div>
  <div class="header-cta">Book now</div>
</header>

<section class="section hero" role="img" aria-label="Photo of a bright lodge living room with large windows">
  <nav class="main-nav">
    <a class="active">Home</a><a>Available dates</a><a>Caravans</a><a>Lodges</a><a>Late deals</a><a>About us</a><a>Contact</a>
  </nav>
</section>

<section class="section intro">
  <p>Pinebrook Stays offers peaceful lodge and caravan holidays surrounded by woodland, lakes and open countryside.</p>
  <p>Families return every year for the space, the quiet and the friendly welcome on site.</p>
</section>

<section class="section deals">
  <h2 class="section-title">Late Deals on Lodges &amp; Caravans</h2>
  <div class="card-row">
    <div class="card"><div class="card-photo" role="img" aria-label="Photo of a lodge interior"></div><div class="card-title">Willow Lodge</div><div class="card-meta">Sleeps 6 · 3 nights<br>From <b>£249</b></div></div>
    <div class="card"><div class="card-photo" role="img" aria-label="Photo of a caravan lounge"></div><div class="card-title">Birch Caravan</div><div class="card-meta">Sleeps 4 · 4 nights<br>From <b>£199</b></div></div>
    <div class="card"><div class="card-photo" role="img" aria-label="Photo of a lodge bedroom"></div><div class="card-title">Oak Retreat</div><div class="card-meta">Sleeps 8 · 7 nights<br>From <b>£489</b></div></div>
    <div class="card"><div class="card-photo" role="img" aria-label="Photo of a caravan kitchen"></div><div class="card-title">Maple Caravan</div><div class="card-meta">Sleeps 6 · 3 nights<br>From <b>£179</b></div></div>
    <div class="card"><div class="card-photo" role="img" aria-label="Photo of a lodge dining area"></div><div class="card-title">Cedar Lodge</div><div class="card-meta">Sleeps 4 · 5 nights<br>From <b>£329</b></div></div>
  </div>
</section>

<section class="section search-band">
  <h3>Find your holiday</h3>
  <div class="search-form">
    <div class="search-field wide">Lodge or caravan</div>
    <div class="search-field mid">Check in</div>
    <div class="search-field mid">Nights</div>
    <div class="search-field mid">Guests</div>
    <div class="search-btn">Search</div>
  </div>
</section>

<section class="section reviews-strip">
  <h2 class="section-title">Popular Stays</h2>
  <div class="card-row">
    <div class="card"><div class="card-photo" role="img" aria-label="Photo of a lodge living room"></div><div class="card-title">Fern Lodge</div><div class="card-meta">Sleeps 6 · hot tub<br>From <b>£299</b></div></div>
    <div class="card"><div class="card-photo" role="img" aria-label="Photo of a caravan interior"></div><div class="card-title">Heather Caravan</div><div class="card-meta">Sleeps 4 · lake view<br>From <b>£219</b></div></div>
    <div class="card"><div class="card-photo" role="img" aria-label="Photo of a lodge lounge"></div><div class="card-title">Pine Lodge</div><div class="card-meta">Sleeps 8 · garden<br>From <b>£399</b></div></div>
    <div class="card"><div class="card-photo" role="img" aria-label="Photo of a lodge bedroom"></div><div class="card-title">Ash Retreat</div><div class="card-meta">Sleeps 6 · decking<br>From <b>£279</b></div></div>
    <div class="card"><div class="card-photo" role="img" aria-label="Photo of a caravan lounge"></div><div class="card-title">Rowan Caravan</div><div class="card-meta">Sleeps 4 · pet friendly<br>From <b>£189</b></div></div>
  </div>
</section>

<section class="section lower">
  <div class="col col-reviews">
    <h4>Guest Reviews</h4>
    <div class="review"><span class="stamp"></span><p>“Lovely clean lodge and a calm site. The children loved the woodland walks.” – Sarah</p></div>
    <div class="review"><span class="stamp"></span><p>“Easy booking, warm welcome and a great caravan. We will be back next summer.” – Mark</p></div>
  </div>
  <div class="col col-news">
    <h4>Latest News</h4>
    <div class="news-item"><span class="date">12 May</span> – New lakeside lodges open for the summer season.</div>
    <div class="news-item"><span class="date">28 Apr</span> – Family fun days return every Saturday in August.</div>
    <div class="news-item"><span class="date">09 Apr</span> – Short breaks now available from two nights.</div>
  </div>
  <div class="col col-side">
    <div class="side-head">Recently viewed</div>
    <div class="side-item"><span class="side-thumb" role="img" aria-label="Lodge thumbnail"></span>Willow Lodge · £249</div>
    <div class="side-item"><span class="side-thumb" role="img" aria-label="Caravan thumbnail"></span>Birch Caravan · £199</div>
    <div class="side-item"><span class="side-thumb" role="img" aria-label="Lodge thumbnail"></span>Oak Retreat · £489</div>
    <div class="side-item"><span class="side-thumb" role="img" aria-label="Caravan thumbnail"></span>Maple Caravan · £179</div>
  </div>
</section>

<footer class="section site-footer">
  <div class="fcol f-news"><h5>Newsletter</h5><p>Get late deals first.</p><div class="f-input"></div><div class="f-btn">Subscribe</div></div>
  <div class="fcol f-links"><h5>Holidays</h5><p>Lodges</p><p>Caravans</p><p>Late deals</p><p>Available dates</p></div>
  <div class="fcol f-more"><h5>Company</h5><p>About us</p><p>Reviews</p><p>News</p></div>
  <div class="fcol f-info"><h5>Contact</h5><p>+44 1632 960418</p><p>hello@pinebrookstays.com</p><p>www.pinebrookstays.com</p></div>
  <div class="fcol f-social"><h5>Follow</h5><div class="social-dot"></div><div class="social-dot"></div><div class="social-dot"></div></div>
  <div class="copyright">© Pinebrook Stays. All rights reserved.</div>
</footer>

<div class="veil"></div>
<div class="modal">
  <div class="modal-photo" role="img" aria-label="Photo of a modern holiday villa with a swimming pool at dusk"></div>
  <div class="modal-form">
    <div class="modal-input">Enter your email address</div>
    <div class="modal-submit">SUBMIT</div>
  </div>
  <svg class="modal-close" viewBox="0 0 30 30" aria-label="Close">
    <circle cx="15" cy="15" r="13" fill="#fff" stroke="#2c2f31" stroke-width="2"/>
    <path d="M10 10l10 10M20 10L10 20" stroke="#2c2f31" stroke-width="2.5"/>
  </svg>
</div>

</body>
</html>
```